Brovanek Data Yellow rose letterhead

I have a new logo for my company but in its current form it is too large to be used on letterhead or as a email signature. I need to have the designer use elements from the current logo and create something close to the original but more suited for smaller items.
Updates

I just uploaded a copy of our logo that does not have the weathered affect. Thanks

Reason: More time for revisions

Industry/Entity Type

It Company

Requirements
Must have
• The design must maintain the visual effect of the current logo. It needs to include the yellow rose and the name of the company.
Nice to have
• It would be nice to maintain the stamp theme and incorporate my name, address, phone, email. etc.

```html
<!DOCTYPE html>
<html lang="en">
<head>
<meta charset="utf-8">
<title>Brovanek Data Letterhead</title>
<link rel="stylesheet" href="https://fonts.googleapis.com/css2?family=Questrial&display=swap">
<style>
  :root {
    --backdrop: #e9e6e2;
    --paper: #ffffff;
    --teal: #3ab8bf;
    --charcoal: #574e4a;
    --brand-brown: #4b3f3a;
    --brand-orange: #e8892a;
    --ink: #1e1e1e;
  }
  * { margin: 0; padding: 0; box-sizing: border-box; }
  html, body {
    width: 1054px;
    height: 1200px;
    overflow: hidden;
    background: var(--backdrop);
    font-family: "Questrial", "Helvetica Neue", Arial, sans-serif;
  }
  .letterhead {
    position: absolute;
    left: 127px;
    top: 35px;
    width: 800px;
    height: 1130px;
    background: var(--paper);
    overflow: hidden;
    box-shadow: 0 4px 14px rgba(0,0,0,0.18);
  }
  .header-band, .footer-band {
    position: absolute;
    left: 0;
    width: 800px;
    display: block;
  }
  .header-band { top: 0; height: 110px; }
  .footer-band { bottom: 0; height: 50px; }
  .brand {
    position: absolute;
    left: 44px;
    top: 34px;
    display: flex;
    align-items: center;
    gap: 14px;
  }
  .brand-square {
    width: 34px;
    height: 34px;
    background: var(--brand-orange);
  }
  .brand-name {
    font-size: 34px;
    color: var(--brand-brown);
    letter-spacing: 0.5px;
    background: var(--paper);
    padding: 4px 10px;
  }
  .contact {
    position: absolute;
    right: 43px;
    top: 966px;
    text-align: right;
    font-style: normal;
    color: var(--ink);
    font-size: 17.5px;
    line-height: 23px;
    letter-spacing: 0.4px;
  }
  .contact .person { font-size: 15.5px; }
</style>
</head>
<body>
  <main class="letterhead">
    <svg class="header-band" viewBox="0 0 800 110" preserveAspectRatio="none" aria-hidden="true">
      <path d="M0 0 H800 V100 C600 60 260 38 0 48 Z" fill="var(--teal)"/>
    </svg>

    <div class="brand">
      <span class="brand-square"></span>
      <span class="brand-name">Brovanek Data</span>
    </div>

    <address class="contact">
      <div class="person">Maren Holtz, PhD</div>
      <div>418 Caldera Ridge Road, Ste 210</div>
      <div>Pine Hollow, TX 75961</div>
      <div>1-800-555-0147</div>
      <div>maren@brovanek-data.com</div>
    </address>

    <svg class="footer-band" viewBox="0 0 800 50" preserveAspectRatio="none" aria-hidden="true">
      <defs>
        <linearGradient id="footer-fade" x1="0" y1="0" x2="1" y2="0">
          <stop offset="0" stop-color="var(--teal)"/>
          <stop offset="0.45" stop-color="var(--teal)"/>
          <stop offset="0.8" stop-color="var(--charcoal)"/>
          <stop offset="1" stop-color="var(--charcoal)"/>
        </linearGradient>
      </defs>
      <path d="M0 30 C260 36 560 28 800 4 V50 H0 Z" fill="url(#footer-fade)"/>
    </svg>
  </main>
</body>
</html>
```